Fresh, modern, fun business card for pediatric dental practice

Need a business card for fresh, modern, fun pediatric dental practice

Clean look that matches our website's font and colors

We prefer the look of curved corners on business cards

Target Market(s)

parents (mothers) of young children, professionals, mid-high class

Industry/Entity Type

Dental

Contact Information for Business Card

Maplebrook Pediatric Dentistry
482 Quarry Lane
Suite 517
Fernhollow, PA 19999
555.555.0193
www.maplebrookkidsdental.example

Mei-Ran Tsai, DMD
Corinne Walbeck, DMD
(we are working on our email address, but we would like that on the card as well)

Font styles to use
Sans Serif

Requirements
Must have
• All info; we would also like to make cards for individual staff members
• colors from our website and color palatte, attatched
• use same font and design as website for branding
Nice to have
• clean, simple card that has a pop of color
• we would like to see a few designs with our tag line "where smiles get brighter"
• we are not sure if we want to have it on there or not
• we would like to see a few designs incorporating the ribbon graphic on our website where the word WELCOME is

```html
<!DOCTYPE html>
<html lang="en">
<head>
<meta charset="utf-8">
<title>Maplebrook Pediatric Dentistry – Business Card</title>
<link href="https://fonts.googleapis.com/css2?family=Lato:wght@400;700&display=swap" rel="stylesheet">
<style>
  :root {
    --backdrop: #e6e2dc;
    --card: #f6f3ee;
    --magenta: #c41f6f;
    --magenta-light: #d8418f;
    --gold: #d9a01c;
    --gold-light: #ecc04a;
    --ink: #5b5b5b;
    --on-magenta: #fbe9f2;
  }
  html, body {
    margin: 0;
    width: 1200px;
    height: 1047px;
    overflow: hidden;
    background: var(--backdrop);
    font-family: "Lato", sans-serif;
  }
  .card {
    position: absolute;
    left: 100px;
    top: 237px;
    width: 1000px;
    height: 572px;
    border-radius: 28px;
    background: var(--card);
    overflow: hidden;
    box-shadow: 0 10px 30px rgba(0,0,0,0.12);
  }
  .card__band {
    position: absolute;
    inset: 0;
    width: 1000px;
    height: 572px;
  }
  .brand {
    position: absolute;
    left: 58px;
    top: 120px;
    color: var(--gold);
    font-weight: 700;
    line-height: 1;
  }
  .brand__name { font-size: 58px; letter-spacing: 1px; }
  .brand__sub { font-size: 30px; margin-top: 10px; letter-spacing: 1px; }
  .person {
    position: absolute;
    right: 57px;
    top: 54px;
    text-align: right;
  }
  .person__name {
    color: var(--gold);
    font-size: 32px;
    font-weight: 700;
    letter-spacing: 1.5px;
    text-transform: uppercase;
  }
  .person__title {
    color: var(--ink);
    font-size: 22px;
    margin-top: 8px;
    letter-spacing: 1px;
  }
  .address {
    position: absolute;
    right: 57px;
    top: 326px;
    text-align: right;
    color: var(--on-magenta);
    font-size: 22px;
    line-height: 31px;
    letter-spacing: 0.5px;
  }
  .contact {
    position: absolute;
    right: 57px;
    top: 405px;
    list-style: none;
    margin: 0;
    padding: 0;
    color: var(--on-magenta);
    font-size: 22px;
    letter-spacing: 0.5px;
  }
  .contact__item {
    display: flex;
    justify-content: flex-end;
    align-items: center;
    gap: 16px;
    height: 31px;
  }
  .contact__icon { width: 18px; height: 18px; flex: none; }
</style>
</head>
<body>
  <div class="card">
    <svg class="card__band" viewBox="0 0 1000 572" aria-hidden="true">
      <defs>
        <linearGradient id="magentaFill" x1="0" y1="1" x2="1" y2="0">
          <stop offset="0" stop-color="var(--magenta-light)"/>
          <stop offset="1" stop-color="var(--magenta)"/>
        </linearGradient>
      </defs>
      <path class="band band--gold" fill="none" stroke="var(--gold)" stroke-width="6"
        d="M0,282 Q500,330 1000,262"/>
      <path class="band band--magenta" fill="url(#magentaFill)"
        d="M0,300 Q500,350 1000,280 L1000,572 L0,572 Z"/>
    </svg>

    <div class="brand">
      <div class="brand__name">Maplebrook</div>
      <div class="brand__sub">pediatric dentistry</div>
    </div>

    <div class="person">
      <div class="person__name">Corinne Walbeck</div>
      <div class="person__title">DMD</div>
    </div>

    <div class="address">
      <div>482 Quarry Lane</div>
      <div>Suite 517 Fernhollow, PA 19999</div>
    </div>

    <ul class="contact">
      <li class="contact__item">
        <span>555.555.0193</span>
        <svg class="contact__icon" viewBox="0 0 24 24" aria-hidden="true"><path fill="var(--gold-light)" d="M6.6 10.8a15.1 15.1 0 0 0 6.6 6.6l2.2-2.2c.3-.3.7-.4 1-.2 1.1.4 2.3.6 3.6.6.6 0 1 .4 1 1V20c0 .6-.4 1-1 1A17 17 0 0 1 3 4c0-.6.4-1 1-1h3.5c.6 0 1 .4 1 1 0 1.3.2 2.5.6 3.6.1.3 0 .7-.2 1z"/></svg>
      </li>
      <li class="contact__item">
        <span>info@maplebrookkidsdental.example</span>
        <svg class="contact__icon" viewBox="0 0 24 24" aria-hidden="true"><rect x="2" y="5" width="20" height="14" rx="1.5" fill="var(--gold-light)"/><path d="M3 6l9 7 9-7" fill="none" stroke="var(--magenta)" stroke-width="1.6"/></svg>
      </li>
      <li class="contact__item">
        <span>www.maplebrookkidsdental.example</span>
        <svg class="contact__icon" viewBox="0 0 24 24" aria-hidden="true"><g fill="none" stroke="var(--gold-light)" stroke-width="2"><circle cx="12" cy="12" r="9"/><ellipse cx="12" cy="12" rx="4" ry="9"/><path d="M3 12h18M5 7h14M5 17h14"/></g></svg>
      </li>
    </ul>
  </div>
</body>
</html>
```